Jolly Paws Business Card Update

I have a business card which I love. I want to keep the same logo, colours, font and style. I want to upgrade the scripting and remove some elements and add others.
On the front side under Services - remove the existing wording and insert - Providing individual coaching strategies to create happy, healthy and social canine companions
Under Denise Carvell amend the current wording to read: Qualified in Dog Behavioural Training, Natural Animal Healthcare and Animal Health Science
On the reverse side to remove the web address.

```html
<!DOCTYPE html>
<html lang="en">
<head>
<meta charset="utf-8">
<title>Jolly Paws Business Card</title>
<link href="https://fonts.googleapis.com/css2?family=Arimo:wght@400;700&family=Open+Sans:wght@400;600&display=swap" rel="stylesheet">
<style>
  :root {
    --bg: #2d2d2d;
    --blue-deep: #1f3f8f;
    --blue-mid: #1f5fb0;
    --blue-light: #0a8fd0;
    --red-deep: #7a1518;
    --red: #cc1f24;
    --cream: #eae4cf;
    --paper: #f1f1f1;
    --navy: #1e2f86;
    --white: #ffffff;
  }
  * { margin: 0; padding: 0; box-sizing: border-box; }
  html, body { width: 1200px; height: 1138px; overflow: hidden; background: var(--bg); }
  .card {
    position: absolute;
    border-radius: 13px;
    overflow: hidden;
    box-shadow: 0 6px 14px rgba(0,0,0,.45);
  }
  /* front */
  .card-front {
    left: 274px; top: 186px; width: 623px; height: 376px;
    background: linear-gradient(225deg, var(--blue-light) 0%, var(--blue-mid) 45%, var(--blue-deep) 100%);
    color: var(--white);
    font-family: "Arimo", Arial, sans-serif;
  }
  .brand-name {
    position: absolute; left: 35px; top: 52px;
    font-family: "Open Sans", Arial, sans-serif;
    font-weight: 600; font-size: 31px; letter-spacing: 1px;
    text-transform: uppercase; color: #e6ebf5;
  }
  .brand-tagline {
    position: absolute; left: 34px; top: 91px;
    font-family: "Open Sans", Arial, sans-serif;
    font-size: 17px; letter-spacing: .3px;
  }
  .services { position: absolute; left: 38px; top: 182px; width: 240px; }
  .services h3 { font-size: 17px; font-weight: 700; }
  .services p { font-size: 16px; line-height: 19px; }
  .emblem { position: absolute; }
  .card-front .emblem { left: 328px; top: 38px; width: 260px; height: 260px; }
  .front-band {
    position: absolute; left: 0; bottom: 0; width: 100%; height: 53px;
    background: linear-gradient(90deg, var(--red-deep) 0%, var(--red) 50%, var(--red-deep) 100%);
    font-size: 16.5px; line-height: 53px; padding-left: 32px; color: #f1e6e6;
  }
  /* back */
  .card-back {
    left: 276px; top: 608px; width: 618px; height: 374px;
    background: var(--paper);
  }
  .back-shape { position: absolute; left: 0; top: 0; }
  .card-back .emblem { left: 36px; top: 91px; width: 194px; height: 194px; }
  .contact {
    position: absolute; right: 27px; top: 34px; text-align: right;
    font-family: "Open Sans", Arial, sans-serif; color: var(--navy);
  }
  .contact .person { font-family: "Arimo", Arial, sans-serif; font-weight: 700; font-size: 25px; line-height: 30px; }
  .contact .quals { font-size: 14px; line-height: 20px; margin-top: 6px; }
  .contact ul { list-style: none; margin-top: 9px; font-size: 15px; line-height: 22px; }
  .contact li { display: flex; justify-content: flex-end; align-items: center; gap: 10px; }
  .contact li svg { width: 14px; height: 14px; }
  .back-services {
    position: absolute; right: 27px; top: 224px; text-align: right;
    font-family: "Arimo", Arial, sans-serif; color: var(--white);
  }
  .back-services h3 { font-size: 16.5px; font-weight: 700; line-height: 19px; }
  .back-services p { font-size: 16px; line-height: 19px; }
  .back-mission {
    position: absolute; right: 27px; top: 324px; text-align: right;
    font-family: "Arimo", Arial, sans-serif; color: var(--navy);
    font-size: 16.5px; line-height: 19px;
  }
  .emblem-name {
    font-family: "Open Sans", Arial, sans-serif; font-weight: 600;
  }
</style>
</head>
<body>

<section class="card card-front">
  <h1 class="brand-name">Jolly Paws</h1>
  <p class="brand-tagline">HAPPY DOGS, HAPPY OWNERS</p>
  <div class="services">
    <h3>SERVICES</h3>
    <p>Providing individual coaching strategies to create happy, healthy and social canine companions</p>
  </div>
  <svg class="emblem" viewBox="0 0 260 260" role="img" aria-label="Jolly Paws brand mark">
    <circle cx="130" cy="130" r="128" fill="var(--red)"/>
    <circle cx="130" cy="130" r="106" fill="var(--cream)"/>
    <text class="emblem-name" x="130" y="138" text-anchor="middle" font-size="26" fill="var(--blue-mid)">Jolly Paws</text>
  </svg>
  <div class="front-band">Promoting communication and connection between dogs and their families</div>
</section>

<section class="card card-back">
  <svg class="back-shape" width="618" height="374" viewBox="0 0 618 374">
    <defs>
      <linearGradient id="backBlue" x1="0" y1="0" x2="1" y2="1">
        <stop offset="0" stop-color="#1f5aae"/>
        <stop offset="1" stop-color="#0b86c8"/>
      </linearGradient>
      <linearGradient id="backRed" x1="0" y1="0" x2="1" y2="0">
        <stop offset="0" stop-color="#7a1518"/>
        <stop offset=".45" stop-color="#cc1f24"/>
        <stop offset="1" stop-color="#8e171b"/>
      </linearGradient>
    </defs>
    <rect x="250" y="216" width="368" height="94" fill="url(#backRed)"/>
    <path d="M0 0 H268 Q360 180 248 374 H0 Z" fill="var(--red-deep)"/>
    <path d="M0 0 H236 Q334 180 215 374 H0 Z" fill="url(#backBlue)"/>
  </svg>
  <svg class="emblem" viewBox="0 0 194 194" role="img" aria-label="Jolly Paws brand mark">
    <circle cx="97" cy="97" r="96" fill="var(--red)"/>
    <circle cx="97" cy="97" r="79" fill="var(--cream)"/>
    <text class="emblem-name" x="97" y="104" text-anchor="middle" font-size="20" fill="var(--blue-mid)">Jolly Paws</text>
  </svg>
  <div class="contact">
    <h2 class="person">Denise Carvell</h2>
    <p class="quals">Qualified in Dog Behavioural<br>Training, Natural Animal Healthcare<br>and Animal Health Science</p>
    <ul>
      <li>0400 271 358
        <svg viewBox="0 0 14 14"><rect x="3" y="0.5" width="8" height="13" rx="1.5" fill="none" stroke="var(--red)" stroke-width="1.5"/><rect x="5" y="2.5" width="4" height="5" fill="var(--red)"/></svg></li>
      <li>jollypaws1@mailbox.com
        <svg viewBox="0 0 14 14"><rect x="0.5" y="3" width="13" height="9" fill="var(--red)"/><path d="M0.5 3 L7 8 L13.5 3" fill="none" stroke="var(--white)" stroke-width="1.2"/></svg></li>
    </ul>
  </div>
  <div class="back-services">
    <h3>SERVICES</h3>
    <p>Providing individual coaching<br>strategies to create happy, healthy<br>and social canine companions</p>
  </div>
  <p class="back-mission">Promoting communication and connection<br>between dogs &amp; their families</p>
</section>

</body>
</html>
```